At Home Pet Euthanasia - business cards & brand stationary

We already have a logo and the colors and a website. Need a business card designed that will be able to customized to multiple veterinarians who will be partnering with us. The feel needs to be compassionate, comforting with our tagline 'A Gift of Love at Home'. It will be 2 sides.
On the back our platform/partner vets will be customizing each business card with their own service areas, phone numbers, name and title. On the front, i would like to see experimentation with use of our photos, the logo, tagline and a description 'Peaceful and Compassionate At-Home Pet Euthanasia'

```html
<!DOCTYPE html>
<html lang="en">
<head>
<meta charset="utf-8">
<title>Evenrest Business Cards</title>
<link rel="stylesheet" href="https://fonts.googleapis.com/css2?family=Raleway:wght@400;500;700&family=Pinyon+Script&display=swap">
<style>
  :root {
    --backdrop: #2a2a2c;
    --brand-blue: #7799c1;
    --brand-blue-deep: #6a8cb6;
    --paper: #ffffff;
    --photo-light: #eef3f8;
    --photo-mid: #d7e2ee;
    --photo-dark: #1d1f24;
  }
  * { box-sizing: border-box; margin: 0; padding: 0; }
  html, body { width: 1200px; height: 960px; overflow: hidden; }
  body {
    background: var(--backdrop);
    font-family: "Raleway", sans-serif;
    position: relative;
  }
  .card {
    position: absolute;
    left: 250px;
    width: 700px;
    height: 400px;
    border-radius: 26px;
    overflow: hidden;
    box-shadow: 0 18px 40px rgba(0,0,0,.45);
  }
  /* Front */
  .card-front { top: 50px; background: var(--paper); }
  .front-photo {
    position: absolute;
    left: 230px; top: 0; right: 0; bottom: 0;
    background:
      radial-gradient(ellipse 170px 200px at 75% 55%, var(--photo-dark) 0 60%, rgba(29,31,36,0) 100%),
      linear-gradient(90deg, var(--photo-light), var(--photo-mid));
  }
  .front-brand {
    position: absolute;
    left: 70px; top: 170px;
    width: 330px;
    color: var(--brand-blue);
  }
  .brand-name {
    display: flex; align-items: center; gap: 12px;
    font-family: "Raleway", sans-serif;
    font-weight: 700;
    font-size: 58px;
    line-height: 1;
  }
  .brand-dot {
    width: 22px; height: 22px; border-radius: 50%;
    background: var(--brand-blue);
    flex: none;
  }
  .tagline {
    font-weight: 500;
    font-size: 17px;
    margin: 8px 0 0 36px;
  }
  .front-description {
    font-family: "Pinyon Script", cursive;
    font-size: 34px;
    line-height: 1.05;
    color: var(--brand-blue);
    margin-top: 32px;
  }
  .front-description span { display: block; }
  .front-description span + span { padding-left: 24px; }

  /* Back */
  .card-back { top: 500px; background: var(--brand-blue); color: var(--paper); }
  .back-details {
    position: absolute;
    left: 60px; top: 70px;
    width: 330px;
  }
  .back-details .brand-name { font-size: 62px; }
  .back-details .brand-dot { background: var(--paper); }
  .back-details .tagline { font-size: 18px; margin-left: 36px; }
  .person { margin-top: 34px; }
  .person-name { font-weight: 700; font-size: 22px; letter-spacing: .5px; }
  .person-title { font-size: 17px; margin-top: 2px; }
  .contact { list-style: none; margin-top: 22px; font-size: 16px; line-height: 1.35; }
  .contact li { display: flex; gap: 10px; align-items: flex-start; }
  .contact li + li { margin-top: 2px; }
  .contact .address { margin-bottom: 10px; }
  .contact svg { width: 14px; height: 14px; flex: none; margin-top: 3px; fill: var(--paper); }
  .back-mark {
    position: absolute;
    right: 70px; top: 80px;
    width: 240px; height: 240px;
    background: var(--paper);
  }
</style>
</head>
<body>
  <section class="card card-front">
    <div class="front-photo" role="img" aria-label="Photo of an older black dog with a pale blue collar, in profile, on a soft light background"></div>
    <div class="front-brand">
      <div class="brand-name"><span class="brand-dot"></span>Evenrest</div>
      <p class="tagline">A gift of love at home.</p>
      <p class="front-description">
        <span>Peaceful &amp; Compassionate</span>
        <span>At-Home Pet Euthanasia</span>
      </p>
    </div>
  </section>

  <section class="card card-back">
    <div class="back-details">
      <div class="brand-name"><span class="brand-dot"></span>Evenrest</div>
      <p class="tagline">A gift of love at home.</p>
      <div class="person">
        <p class="person-name">DANIEL REYES</p>
        <p class="person-title">President</p>
      </div>
      <ul class="contact">
        <li class="address">
          <svg viewBox="0 0 14 14"><path d="M7 0a5 5 0 0 0-5 5c0 3.6 5 9 5 9s5-5.4 5-9a5 5 0 0 0-5-5zm0 7a2 2 0 1 1 0-4 2 2 0 0 1 0 4z"/></svg>
          <span>1420 Willow Bend Road<br>Juneau, Alaska 99801</span>
        </li>
        <li>
          <svg viewBox="0 0 14 14"><path d="M3 1l2.2 2.6-1.3 1.7a8 8 0 0 0 4.8 4.8l1.7-1.3L13 11l-1.6 2c-5.6 0-10.4-4.8-10.4-10.4z"/></svg>
          <span>555-014-2273</span>
        </li>
        <li>
          <svg viewBox="0 0 14 14"><path d="M1 3h12v8H1zm1 1v.4l5 3.3 5-3.3V4z"/></svg>
          <span>daniel@evenrest.com</span>
        </li>
        <li>
          <svg viewBox="0 0 14 14"><circle cx="7" cy="7" r="6"/></svg>
          <span>www.evenrest.com</span>
        </li>
      </ul>
    </div>
    <div class="back-mark"></div>
  </section>
</body>
</html>
```